Golden Coat All-Purpose Breading Bag Design

Our client, Halvern Food Products, is looking to re-design the packaging for their product, Pellham's Golden Coat. Goldn Coat is an all-purpose food breading mix.

Halvern Foods has a registered trademark for this product, but they have not been using it for this particular 10 pound bag. They want to get the trademark onto the bag and also give the bag an updated look. They would like to continue to use the same red and blue colors. This 10 pound bag is not available on store shelves; it is sold to food service distributors who sell to restaurants.

All of the copy on the existing bag is still relevant, so we will want to incoprporate it into the bag design. Once these bags are filled with product, the tops get folded over about 1 inch and then sewn shut with thread.

Eventually, we will need the design applied to the Bag Template file attached, but that isn't important until a design is selected.

Target Market(s)

Restaurants

Industry/Entity Type

Food Manufacturing

Colors
0054AA
0677BA
7BADD7
CADEEF
E8F1F8
EB3D1F
EC4F4E
F09395
F8D3D4
FCEDEE

Requirements
Must have
• Trademark introduced to the design

```html
<!DOCTYPE html>
<html lang="en">
<head>
<meta charset="utf-8">
<title>Pellham's Golden Coat – Bag Front</title>
<link rel="stylesheet" href="https://fonts.googleapis.com/css2?family=Barlow+Condensed:ital,wght@1,800&family=Montserrat:wght@700;800&display=swap">
<style>
  :root {
    --navy: #233a84;
    --red: #cd2028;
    --wheat-light: #c9cee2;
    --wheat-mid: #98a3cb;
    --white: #ffffff;
  }
  html, body {
    margin: 0;
    width: 1200px;
    height: 953px;
    overflow: hidden;
    background: var(--white);
  }
  .bag-front {
    display: block;
    margin: 0 auto;
    width: 752px;
    height: 953px;
  }
  .tagline {
    font-family: "Barlow Condensed", sans-serif;
    font-style: italic;
    font-weight: 800;
    font-size: 34px;
    fill: var(--navy);
  }
  .tagline .accent { fill: var(--red); }
  .brand-text {
    font-family: "Montserrat", sans-serif;
    font-weight: 800;
    fill: var(--white);
    text-anchor: middle;
  }
  .descriptor {
    font-family: "Montserrat", sans-serif;
    font-weight: 800;
    font-size: 30px;
    letter-spacing: 1px;
    fill: var(--white);
    text-anchor: middle;
  }
  .panel-text {
    font-family: "Montserrat", sans-serif;
    font-weight: 700;
    fill: var(--white);
    text-anchor: middle;
  }
  .claim { font-size: 24px; letter-spacing: 2.5px; }
  .instructions {
    font-family: "Barlow Condensed", sans-serif;
    font-style: italic;
    font-weight: 800;
    font-size: 22px;
    fill: var(--white);
    text-anchor: middle;
    letter-spacing: .5px;
  }
  .ingredients { font-size: 15.5px; letter-spacing: 1.6px; }
  .net-weight { font-size: 24px; letter-spacing: 2px; }
</style>
</head>
<body>
<svg class="bag-front" viewBox="60 200 930 1178" xmlns="http://www.w3.org/2000/svg">
  <defs>
    <path id="tagline-line-1" d="M285 345 Q520 280 768 282"/>
    <path id="tagline-line-2" d="M335 365 Q540 312 745 322"/>
  </defs>

  <!-- tagline -->
  <text class="tagline"><textPath href="#tagline-line-1">CHICKEN FRIED THE GOLDEN COAT WAY</textPath></text>
  <text class="tagline"><textPath href="#tagline-line-2">IS FRIED CHICKEN <tspan class="accent">THE RIGHT WAY.</tspan></textPath></text>

  <!-- blue panels -->
  <path class="panel-top" fill="var(--navy)" d="M283 415 Q530 350 776 378 L776 600 L283 600 Z"/>
  <rect class="panel-bottom" fill="var(--navy)" x="285" y="900" width="482" height="565"/>

  <!-- red banner -->
  <path class="banner" fill="var(--red)" stroke="var(--white)" stroke-width="6"
        d="M165 615 Q500 528 882 560 L838 921 Q520 905 222 968 Z"/>

  <!-- brand name -->
  <text class="brand-text" x="530" y="505" font-size="76">Pellham's</text>
  <text class="brand-text" x="525" y="730" font-size="118">Golden</text>
  <text class="brand-text" x="640" y="880" font-size="112">Coat</text>

  <text class="descriptor" x="375" y="828">THE ALL</text>
  <text class="descriptor" x="372" y="860">PURPOSE</text>
  <text class="descriptor" x="390" y="892">BREADING</text>

  <!-- product details -->
  <text class="panel-text claim" x="530" y="1025">SEALS JUICE IN – GREASE OUT</text>
  <text class="instructions" x="530" y="1053">COOKS TWO-POUND CHICKEN WELL DONE</text>
  <text class="instructions" x="530" y="1081">IN 10 MINUTES (DEEP FAT).</text>

  <text class="panel-text ingredients" x="530" y="1162">INGREDIENTS: FLOUR, SALT, NON-FAT MILK</text>
  <text class="panel-text ingredients" x="530" y="1189">SOLIDS, EGG YOLK, BAKING POWDER,</text>
  <text class="panel-text ingredients" x="530" y="1216">CORN STARCH, SUGAR AND PEPPER.</text>

  <text class="panel-text net-weight" x="527" y="1341">NET WT. 10 LBS.</text>

  <!-- wheat decoration areas -->
  <g role="img" aria-label="Wheat stalk illustrations, left">
    <rect x="110" y="1072" width="86" height="318" rx="40" fill="var(--wheat-light)"/>
    <rect x="210" y="1135" width="66" height="245" rx="30" fill="var(--wheat-mid)"/>
  </g>
  <g role="img" aria-label="Wheat stalk illustrations, right">
    <rect x="776" y="1072" width="86" height="318" rx="40" fill="var(--wheat-light)"/>
    <rect x="866" y="1135" width="66" height="245" rx="30" fill="var(--wheat-mid)"/>
  </g>
</svg>
</body>
</html>
```